Social Media App Needs PPT Template

We need a PowerPoint template for a new social media company based in the DC area called "Bold Ledger." We provide an interactive digital platform for executives to share actionable advice. We would like to see designs that use our orange logo color as an accent, but are mainly grey, white, and black. The final design should communicate clean, chic, modern, and professional.

Target Market(s)

Executives

Industry/Entity Type

Information Technology

Font styles to use
Sans Serif

Colors
f78f20
fbe7d2
ffffff
000000
e8e8e8
757575

Requirements
Must have
• My project must have title page and many options for the body of the ppt (graphs, tables, etc). It also needs to be easy to modify. I must have someone who is experienced in creating powerpoint templates.
Nice to have
• It would be nice to have a very modern and clean design that includes the logo on every page, but still leaves a lot of room for the content of the slide
Should not have
• My design project should not look to busy.

```html
<!DOCTYPE html>
<html lang="en">
<head>
<meta charset="utf-8">
<title>Bold Ledger – Team Slide</title>
<link href="https://fonts.googleapis.com/css2?family=Lato:wght@300;400;700&display=swap" rel="stylesheet">
<style>
  :root {
    --backdrop: #cbcbcb;
    --navy: #222b3a;
    --orange: #f7931e;
    --white: #ffffff;
    --ink: #2a2f3a;
    --muted: #6f6f6f;
    --rule: #5b6478;
  }
  * { margin: 0; padding: 0; box-sizing: border-box; }
  html, body {
    width: 1200px; height: 960px; overflow: hidden;
    background: var(--backdrop);
    font-family: 'Lato', sans-serif;
  }
  .canvas { position: relative; width: 1200px; height: 960px; }
  .page-label {
    position: absolute; top: 66px; left: 0; width: 1237px;
    text-align: center; color: var(--white);
    font-weight: 300; font-size: 32px; letter-spacing: 1px;
  }
  .slide {
    position: absolute; left: 120px; top: 143px;
    width: 958px; height: 718px; background: var(--white);
  }
  .sidebar {
    position: absolute; left: 0; top: 0; width: 170px; height: 100%;
    background: var(--navy);
  }
  .brand {
    position: absolute; top: 40px; left: 0; width: 100%;
    display: flex; flex-direction: column; align-items: center; gap: 12px;
  }
  .brand-dot { width: 46px; height: 46px; border-radius: 50%; background: var(--orange); }
  .brand-name { color: var(--white); font-weight: 700; font-size: 21px; letter-spacing: 0.5px; }
  .site-url {
    position: absolute; left: 19px; bottom: 27px;
    color: var(--white); font-weight: 300; font-size: 18px;
  }
  .slide-title {
    position: absolute; left: 205px; top: 97px;
    color: var(--orange); font-weight: 400; font-size: 40px;
  }
  .title-rule {
    position: absolute; left: 205px; top: 154px; width: 716px;
    height: 1px; background: var(--orange);
  }
  .member { position: absolute; width: 360px; height: 220px; }
  .member-photo { position: absolute; left: 0; top: 0; width: 119px; height: 134px; }
  .photo-a { background: linear-gradient(135deg, #dfe7ee 0%, #8a7a6c 55%, #2a2d35 100%); }
  .photo-b { background: linear-gradient(135deg, #c9a24a 0%, #b48a66 50%, #9fb4d0 100%); }
  .photo-c { background: linear-gradient(135deg, #c9c9c9 0%, #a88a74 55%, #3a3a3a 100%); }
  .photo-d { background: linear-gradient(135deg, #e7ece9 0%, #c49a80 55%, #c9d6e6 100%); }
  .member-info { position: absolute; left: 134px; top: 4px; width: 188px; }
  .member-name { color: var(--ink); font-weight: 700; font-size: 22px; line-height: 1; padding-left: 2px; }
  .member-role { color: var(--muted); font-weight: 300; font-size: 15px; margin-top: 10px; }
  .member-bio {
    color: #3b3f48; font-size: 13.6px; line-height: 17.1px;
    margin-top: 12px; text-align: justify;
  }
  .m1 { left: 206px; top: 193px; }
  .m2 { left: 599px; top: 193px; }
  .m3 { left: 206px; top: 434px; }
  .m4 { left: 599px; top: 434px; }
  .footer-rule {
    position: absolute; left: 802px; top: 664px; width: 124px;
    height: 1px; background: var(--rule);
  }
  .page-number {
    position: absolute; right: 35px; top: 681px;
    color: var(--muted); font-size: 13px;
  }
</style>
</head>
<body>
<div class="canvas">
  <div class="page-label">Page 8</div>
  <section class="slide">
    <aside class="sidebar">
      <div class="brand">
        <span class="brand-dot"></span>
        <span class="brand-name">Bold Ledger</span>
      </div>
      <div class="site-url">boldledger.com</div>
    </aside>

    <h1 class="slide-title">Title of the page</h1>
    <div class="title-rule"></div>

    <article class="member m1">
      <div class="member-photo photo-a" role="img" aria-label="Portrait photo of a bearded man in a dark suit"></div>
      <div class="member-info">
        <h2 class="member-name">Mr A. Smilth</h2>
        <p class="member-role">(President)</p>
        <p class="member-bio">Lorem ipsum dolor sit amet, consectetuer adipiscing elit, sed diam nonummy nibh euismod tincidunt ut laoreet dolore magna aliquam erat volutpat. Ut wisi enim ad minim veniam, quis nostrud exercitation.</p>
      </div>
    </article>

    <article class="member m2">
      <div class="member-photo photo-c" role="img" aria-label="Portrait photo of a smiling man against a grey backdrop"></div>
      <div class="member-info">
        <h2 class="member-name">Mr C. Smilth</h2>
        <p class="member-role">(President)</p>
        <p class="member-bio">Lorem ipsum dolor sit amet, consectetuer adipiscing elit, sed diam nonummy nibh euismod tincidunt ut laoreet dolore magna aliquam erat volutpat. Ut wisi enim ad minim veniam, quis nostrud exercitation.</p>
      </div>
    </article>

    <article class="member m3">
      <div class="member-photo photo-b" role="img" aria-label="Profile photo of a smiling man outdoors in a light blue suit"></div>
      <div class="member-info">
        <h2 class="member-name">Mr B. Smilth</h2>
        <p class="member-role">(President)</p>
        <p class="member-bio">Lorem ipsum dolor sit amet, consectetuer adipiscing elit, sed diam nonummy nibh euismod tincidunt ut laoreet dolore magna aliquam erat volutpat. Ut wisi enim ad minim veniam, quis nostrud exercitation.</p>
      </div>
    </article>

    <article class="member m4">
      <div class="member-photo photo-d" role="img" aria-label="Portrait photo of a smiling man in a light shirt"></div>
      <div class="member-info">
        <h2 class="member-name">Mr D. Smilth</h2>
        <p class="member-role">(President)</p>
        <p class="member-bio">Lorem ipsum dolor sit amet, consectetuer adipiscing elit, sed diam nonummy nibh euismod tincidunt ut laoreet dolore magna aliquam erat volutpat. Ut wisi enim ad minim veniam, quis nostrud exercitation.</p>
      </div>
    </article>

    <div class="footer-rule"></div>
    <div class="page-number">Page 7</div>
  </section>
</div>
</body>
</html>
```